Salon and Spa Distributor Business Card

Need a business card. We are are distributor in the salon and spa industry. We identify with natural beauty. Need a card with:
Company Name: Petal Quarry"
Title: "President & CEO"
Address
Company Phone number
email
website
Tag Line:" The Professional Salon Source"

Industry/Entity Type

Business

Contact Information for Business Card

Name: Dov Strommen
Title: "President & CEO"
Address: 31 Harlow Ln, Bexmoor, NJ 07813
Company Phone number: 800-463-5918
email: dovstrommen@petalquarry.example
website: www.petalquarry.example

Requirements
Should not have
• No black backgrounds

```html
<!DOCTYPE html>
<html lang="en">
<head>
<meta charset="utf-8">
<title>Petal Quarry – Business Card</title>
<link rel="stylesheet" href="https://fonts.googleapis.com/css2?family=Questrial&family=Arimo:ital,wght@0,400;0,700;1,400&display=swap">
<style>
  :root {
    --canvas-bg: #e6e6e6;
    --green-deep: #005a28;
    --green-mid: #2f7f3c;
    --green-bright: #3fb93a;
    --green-text: #1f8a2e;
    --name-green: #0f6b2a;
    --white: #ffffff;
    --card-white: #f4f4f4;
    --text-dark: #333333;
    --text-grey: #444444;
  }
  * { margin: 0; padding: 0; box-sizing: border-box; }
  html, body { width: 1200px; height: 576px; overflow: hidden; }
  body {
    background: var(--canvas-bg);
    position: relative;
    font-family: "Questrial", sans-serif;
  }
  .card {
    position: absolute;
    top: 138px;
    width: 484px;
    height: 292px;
    border-radius: 12px;
    overflow: hidden;
  }
  .card-back {
    left: 82px;
    background: linear-gradient(180deg, var(--green-deep) 0%, var(--green-mid) 100%);
  }
  .card-front {
    left: 602px;
    width: 480px;
    background: linear-gradient(180deg, var(--white) 0%, var(--card-white) 100%);
  }
  .brand {
    position: absolute;
    display: flex;
    align-items: center;
    gap: 14px;
    font-family: "Questrial", sans-serif;
    white-space: nowrap;
  }
  .brand-mark { border-radius: 50%; flex: none; }
  .card-back .brand {
    left: 0; right: 0; top: 166px;
    justify-content: center;
    color: var(--white);
    font-size: 30px;
  }
  .card-back .brand-mark { width: 34px; height: 34px; background: var(--white); }
  .front-art { position: absolute; inset: 0; }
  .tagline {
    position: absolute;
    right: 26px; top: 26px;
    text-align: right;
    color: var(--white);
    font-family: "Arimo", sans-serif;
    font-style: italic;
    font-size: 13px;
    line-height: 18px;
  }
  .card-front .brand {
    left: 24px; top: 104px;
    gap: 20px;
    color: var(--green-text);
    font-size: 32px;
  }
  .card-front .brand-mark { width: 56px; height: 56px; background: var(--green-text); }
  .holder { position: absolute; left: 28px; top: 228px; }
  .holder-name {
    font-family: "Arimo", sans-serif;
    font-weight: 700;
    font-size: 19px;
    color: var(--name-green);
    line-height: 24px;
  }
  .holder-title {
    font-family: "Arimo", sans-serif;
    font-size: 11px;
    color: var(--text-grey);
    margin-top: 2px;
  }
  .contact {
    position: absolute;
    right: 22px; top: 194px;
    list-style: none;
    font-family: "Arimo", sans-serif;
    font-size: 13px;
    color: var(--text-dark);
    text-align: right;
  }
  .contact li {
    display: flex;
    justify-content: flex-end;
    align-items: center;
    gap: 5px;
    height: 18px;
  }
  .contact svg { width: 10px; height: 10px; flex: none; }
</style>
</head>
<body>
  <section class="card card-back" aria-label="Card back">
    <div class="brand"><span class="brand-mark"></span><span class="brand-name">Petal Quarry</span></div>
  </section>

  <section class="card card-front" aria-label="Card front">
    <svg class="front-art" viewBox="0 0 480 292" width="480" height="292" aria-hidden="true">
      <path d="M0,0 H480 V106 C380,92 320,42 200,24 C120,12 50,20 0,36 Z" fill="var(--green-deep)"/>
      <path d="M0,44 C70,22 150,18 230,34 C150,26 70,32 0,52 Z" fill="var(--white)" opacity="0.85"/>
      <path d="M20,54 C150,14 300,58 480,116 V126 C300,70 150,30 20,54 Z" fill="var(--green-bright)"/>
    </svg>
    <p class="tagline">The Professional<br>Salon Source</p>
    <div class="brand"><span class="brand-mark"></span><span class="brand-name">Petal Quarry</span></div>
    <div class="holder">
      <p class="holder-name">Dov Strommen</p>
      <p class="holder-title">President &amp; CEO</p>
    </div>
    <ul class="contact">
      <li>800-463-5918
        <svg viewBox="0 0 10 10" aria-hidden="true"><path d="M1,3 Q5,0 9,3 L8,4.5 L6.5,3.6 V3 H3.5 V3.6 L2,4.5 Z M2.5,5 H7.5 L8.5,9 H1.5 Z" fill="var(--name-green)"/></svg>
      </li>
      <li>www.petalquarry.example
        <svg viewBox="0 0 10 10" aria-hidden="true"><rect x="0.5" y="2" width="9" height="6.5" fill="var(--name-green)"/><path d="M0.8,2.3 L5,5.6 L9.2,2.3" fill="none" stroke="var(--white)" stroke-width="0.9"/></svg>
      </li>
      <li>dovstrommen@petalquarry.example
        <svg viewBox="0 0 10 10" aria-hidden="true"><circle cx="5" cy="5" r="4.3" fill="none" stroke="var(--name-green)" stroke-width="1.2"/><ellipse cx="5" cy="5" rx="1.8" ry="4.3" fill="none" stroke="var(--name-green)" stroke-width="0.9"/><path d="M0.8,5 H9.2" stroke="var(--name-green)" stroke-width="0.9"/></svg>
      </li>
      <li>31 Harlow Ln, Bexmoor, NJ 07813</li>
    </ul>
  </section>
</body>
</html>
```